Visitenkarte für Ergotherapiepraxis
Zielgruppe
Wir arbeiten mit Kindern und Erwachsene jeden Alters.
Diese Personen kommen mit Beeinträchtigungen (körperlich, seelisch, schulisch) im täglichen Leben zu uns. Wir unterstützen unsere Patienten die Beeinträchtigungen zu verringern oder zu kompensieren und so den Alltag besser bewältigen zu können.
Aufgabenstellung
Ein Design was Kinder und Erwachsene anspricht, aber nicht zu verspielt wirkt. Es soll vertrauenserweckend sein. Eventuell sollte die Visitenkarte ein "aufgehendes oder erblühendes oder aufsteigendes" Element enthalten (=zu Beginn war die Beeinträchtigung dann steigt die Lebensqualität als Folge der Behandlung)
Daten vorn:
Ergotherapiepraxis

```html
<!DOCTYPE html>
<html lang="de">
<head>
<meta charset="utf-8">
<title>Visitenkarte Ergotherapiepraxis</title>
<link rel="stylesheet" href="https://fonts.googleapis.com/css2?family=Barlow:wght@300;400;500&display=swap">
<style>
  :root {
    --plum: #84656f;
    --ochre: #d4955a;
    --peach: #fad5a6;
    --ink: #555456;
    --white: #ffffff;
    --ghost: #efefef;
    --frame: #1a1a1a;
  }
  * { margin: 0; padding: 0; box-sizing: border-box; }
  html, body { width: 923px; height: 1200px; overflow: hidden; background: var(--white); }
  body { position: relative; font-family: "Barlow", sans-serif; }

  .card {
    position: absolute; left: 13px; width: 904px;
    border: 2px solid var(--frame); background: var(--white); overflow: hidden;
  }
  .card--front { top: 2px; height: 586px; }
  .card--back { top: 614px; height: 584px; }

  .band { position: absolute; left: 0; right: 0; }
  .band--main { top: 372px; height: 131px; background: var(--plum); }
  .band--foot { top: 558px; bottom: 0; background: var(--plum); }
  .band--name { top: 397px; height: 97px; background: var(--peach); }

  .brand-mark {
    position: absolute; left: 60px; top: 150px;
    display: flex; align-items: center; gap: 14px;
    font-size: 56px; font-weight: 500; letter-spacing: 1px; line-height: 1;
  }
  .brand-mark__dot { width: 36px; height: 36px; border-radius: 50%; background: currentColor; }
  .card--front .brand-mark { color: var(--plum); }
  .card--back .brand-mark { color: var(--ghost); }

  .practice-title {
    position: absolute; left: 380px; top: 318px; font-size: 47px; line-height: 1;
    font-weight: 500; color: var(--ink); white-space: nowrap;
  }
  .therapist-name {
    position: absolute; left: 380px; top: 378px; font-size: 46px; font-weight: 500;
    line-height: 1.2; color: var(--white); white-space: nowrap;
  }
  .phone {
    position: absolute; left: 382px; top: 460px; font-size: 33px; font-weight: 500;
    line-height: 1.2; color: var(--white); white-space: nowrap;
  }
  .address {
    position: absolute; left: 0; right: 64px; top: 510px; text-align: right;
    font-size: 38px; font-weight: 500; line-height: 1.2; color: var(--ochre); white-space: nowrap;
  }

  .label {
    position: absolute; right: 64px; top: 350px; font-size: 35px; line-height: 1.2;
    font-weight: 500; color: var(--ink); white-space: nowrap;
  }
</style>
</head>
<body>
  <section class="card card--front" aria-label="Vorderseite">
    <div class="band band--main"></div>
    <div class="band band--foot"></div>
    <div class="brand-mark"><span class="brand-mark__dot"></span>Lorenz</div>
    <h1 class="practice-title">Ergotherapiepraxis</h1>
    <p class="therapist-name">Sabine Lorenz</p>
    <p class="phone">Tel. 033845/47190</p>
    <p class="address">Am Lindenweg 4 | 14947 Nuthetal, OT Birkau</p>
  </section>

  <section class="card card--back" aria-label="Rückseite">
    <div class="brand-mark"><span class="brand-mark__dot"></span>Lorenz</div>
    <p class="label">Behandelnder Therapeut:</p>
    <div class="band band--name"></div>
  </section>
</body>
</html>
```